RW Holloway LLC Business Card - Civil Engineering & Consulting Firm

We need a Business Card that is elegant, and masculine.  It is our Professional Civil Engineering & Consulting Company located in San Antonio TX (Not s construction or builder firm- no gears & no tool images please). We provide civil engineering services including  commercial site plans, grading and drainage plans, utility plans, hydraulics and hydrology, land planning, utility coordination, and other general civil engineering services related to commercial and residential development.
We have 2 existing Logos. We would like to convey reliability, strength, trustworthiness and attention to detail.  Blues and orange tones as per logo We are OK with the use of a darker blue in the mix.  We have 2 logo versions - Full Company Name Logo to go on the back of card, & Small Icon Logo for the front w/ personal Info.

Target Market(s)
Architects, Real Estate Developers, Other Strctural Engineers, Surveyers, General Contractors
Industry/Entity Type
Professional Civil Engineering
Contact Information for Business Card
Name, Position, Address, Cell & Office #, email, and company website
Font styles to use
Other font styles liked:
- Avian
Requirements
Should not have
- No Tools, No Gears, no Cranes, or Construction Equipment.

```html
<!DOCTYPE html>
<html lang="en">
<head>
<meta charset="UTF-8">
<title>RW Holloway LLC – Business Card</title>
<link href="https://fonts.googleapis.com/css2?family=Montserrat:wght@400;500;700;800&display=swap" rel="stylesheet">
<style>
  :root {
    --backdrop: #1f1f21;
    --card-white: #ffffff;
    --card-shade: #eeeeee;
    --brand-orange: #ee912d;
    --brand-blue: #78acd9;
    --brand-yellow: #f7c11a;
    --ink: #1b1b1b;
    --gradient-mid: #b2a795;
  }
  * { margin: 0; padding: 0; box-sizing: border-box; }
  html, body {
    width: 1200px; height: 900px; overflow: hidden;
    background: var(--backdrop);
    font-family: "Montserrat", sans-serif;
  }
  .canvas {
    width: 1200px; height: 900px;
    display: flex; flex-direction: column; align-items: center; justify-content: center;
    gap: 48px;
  }
  .card {
    position: relative;
    width: 640px; height: 366px;
    border-radius: 26px;
    overflow: hidden;
    box-shadow: 0 10px 30px rgba(0,0,0,.5);
  }
  /* Front */
  .card-front {
    background: linear-gradient(180deg, var(--card-white) 60%, var(--card-shade));
  }
  .front-bands { position: absolute; inset: 0; width: 100%; height: 100%; }
  .front-brand {
    position: absolute; left: 50px; top: 150px;
    display: flex; align-items: center; gap: 12px;
    font-weight: 700; font-size: 22px; color: var(--brand-orange);
  }
  .front-brand .brand-square {
    width: 18px; height: 18px; background: var(--brand-blue);
  }
  .divider {
    position: absolute; left: 318px; top: 40px;
    width: 2px; height: 250px; background: var(--brand-orange);
  }
  .details {
    position: absolute; left: 348px; top: 48px;
    color: var(--ink);
  }
  .person-name {
    font-weight: 800; font-size: 24px; color: var(--brand-orange);
    text-transform: uppercase; letter-spacing: .5px;
  }
  .person-title { font-size: 17px; font-weight: 500; margin-top: 4px; }
  .address { font-size: 16px; font-weight: 500; line-height: 1.35; margin-top: 18px; }
  .contact-list { list-style: none; margin-top: 16px; }
  .contact-list li {
    display: flex; align-items: center; gap: 10px;
    font-size: 16px; font-weight: 500; line-height: 1.55;
  }
  .contact-list svg { width: 16px; height: 16px; flex: none; }
  /* Back */
  .card-back {
    background: linear-gradient(200deg, var(--brand-blue) 0%, var(--gradient-mid) 50%, var(--brand-orange) 100%);
    display: flex; align-items: center; justify-content: center;
  }
  .back-brand {
    color: var(--card-white);
    font-weight: 500; font-size: 48px; letter-spacing: 4px;
    text-transform: uppercase;
  }
</style>
</head>
<body>
<main class="canvas">
  <section class="card card-front" aria-label="Business card front">
    <svg class="front-bands" viewBox="0 0 640 366" preserveAspectRatio="none" aria-hidden="true">
      <polygon points="0,312 180,312 205,328 0,328" fill="var(--brand-orange)"/>
      <polygon points="0,328 205,328 215,322 640,322 640,366 0,366" fill="var(--brand-blue)"/>
      <polygon points="0,160 12,160 12,312 0,312" fill="var(--brand-orange)" opacity="0"/>
    </svg>
    <div class="front-brand"><span class="brand-square"></span>RW Holloway LLC</div>
    <div class="divider"></div>
    <div class="details">
      <h1 class="person-name">Dana Whitfield</h1>
      <p class="person-title">Co-Founder</p>
      <p class="address">1840 Cedar Ridge Drive<br>Suite 210 San Antonio</p>
      <ul class="contact-list">
        <li>
          <svg viewBox="0 0 24 24"><path fill="var(--brand-orange)" d="M6.6 10.8a15.1 15.1 0 0 0 6.6 6.6l2.2-2.2a1 1 0 0 1 1-.25 11.4 11.4 0 0 0 3.6.57 1 1 0 0 1 1 1V20a1 1 0 0 1-1 1A17 17 0 0 1 3 4a1 1 0 0 1 1-1h3.5a1 1 0 0 1 1 1c0 1.25.2 2.45.57 3.57a1 1 0 0 1-.25 1z"/></svg>
          555-210-4471
        </li>
        <li>
          <svg viewBox="0 0 24 24"><rect x="3" y="9" width="18" height="12" rx="2" fill="var(--brand-orange)"/><path d="M2 8c3-4 17-4 20 0v2h-5V8H7v2H2z" fill="var(--brand-orange)"/></svg>
          555-210-4472
        </li>
        <li>
          <svg viewBox="0 0 24 24"><rect x="2" y="5" width="20" height="14" rx="2" fill="var(--brand-orange)"/><path d="M3 6l9 7 9-7" stroke="#fff" stroke-width="1.6" fill="none"/></svg>
          info@rwhollowayllc
        </li>
        <li>
          <svg viewBox="0 0 24 24"><circle cx="12" cy="12" r="10" fill="var(--brand-orange)"/><path d="M2 12h20M12 2c3 3 3 17 0 20M12 2c-3 3-3 17 0 20" stroke="#fff" stroke-width="1.2" fill="none"/></svg>
          www.hollowaycivil.com
        </li>
      </ul>
    </div>
  </section>

  <section class="card card-back" aria-label="Business card back">
    <p class="back-brand">RW Holloway LLC</p>
  </section>
</main>
</body>
</html>
```